Navoro & Omvar Automotive Repair Shop. Need a new website design.

We specialize in Navoro & Omvar auto repair, but also work on other Asian import vehicles. We have been in business for 7 years and pride ourselves on high quality auto repair that is fixed right the first time. Would like the automotive repair website to incorporate the colors black, red and white if possible and have our logo and some Navoro and Omvar vehicles included in the website.

Target Market(s)

Navoro & Omvar vehicle owners

Industry/Entity Type

Automotive Repair

Coding

Coded - Design and coding required

Number of Pages Required

5+ page

Colors
EB3D1F
EC4F4E
F09395
F8D3D4
FCEDEE

Requirements
Must have
• Home, Services, Contact Us, Schedule appointment, and a gallery tab that I can add shop pictures to when completed.
Nice to have
• Would like to see example pictures of job next to each service listed.
Should not have
• Service not related to auto repair. Ex. auto detailing, towing, car wash

```html
<!DOCTYPE html>
<html lang="en">
<head>
<meta charset="utf-8">
<title>Halden Automotive – About Us</title>
<link href="https://fonts.googleapis.com/css2?family=Roboto:wght@400;500;700&display=swap" rel="stylesheet">
<style>
:root{
  --black:#000;
  --white:#fff;
  --red:#e00000;
  --ink:#111;
  --muted:#444;
  --line:#555;
  --sky:#8fb4e0;
  --pavement:#9a9a98;
  --map:#eceef1;
}
*{box-sizing:border-box;margin:0;padding:0}
html,body{width:1200px;height:3239px;overflow:hidden}
body{font-family:"Roboto",Arial,sans-serif;color:var(--ink);background:var(--white);position:relative}
.abs{position:absolute}
a{color:inherit;text-decoration:none}

.site-header{position:absolute;left:0;top:0;width:1200px;height:108px;background:var(--black);color:var(--white)}
.main-nav{position:absolute;left:53px;top:45px;display:flex;gap:27px;font-size:13.5px;text-transform:uppercase}
.main-nav .current{color:var(--red)}
.brand{position:absolute;left:540px;top:38px;width:120px;text-align:center;font-weight:700;font-size:24px;letter-spacing:1px;color:var(--white)}
.header-phone{position:absolute;left:753px;top:45px;font-size:13.5px;display:flex;align-items:center;gap:6px}
.btn{display:inline-flex;align-items:center;justify-content:center;background:var(--red);color:var(--white);font-size:13.5px}
.header-book{position:absolute;left:984px;top:36px;width:163px;height:36px}

.hero-title{position:absolute;left:60px;top:200px;width:1080px;text-align:center;font-weight:700;font-size:48px;line-height:56px}
.hero-text{position:absolute;left:60px;top:334px;width:1080px;text-align:center;font-size:14.5px;line-height:22.5px;color:var(--ink)}
.hero-photo{position:absolute;left:53px;top:490px;width:1094px;height:615px;border-radius:10px;background:linear-gradient(180deg,#6f9fd9 0%,#b9cfe9 22%,#3d3a36 25%,#8a8378 42%,#4a4a48 58%,var(--pavement) 70%,#b4b2ae 100%)}
.hero-actions{position:absolute;left:494px;top:1185px;display:flex;align-items:center;gap:20px}
.hero-actions .btn{width:97px;height:40px}
.learn{font-size:13.5px;display:flex;align-items:center;gap:10px}

.values{position:absolute;left:0;top:1318px;width:1200px;height:686px;background:var(--black);color:var(--white)}
.eyebrow{font-size:12.5px;font-weight:500}
.values .eyebrow{position:absolute;left:53px;top:96px}
.values h2{position:absolute;left:53px;top:126px;width:640px;font-size:40px;line-height:48px;font-weight:700}
.values .lede{position:absolute;left:53px;top:244px;width:630px;font-size:14.5px;line-height:22.5px}
.hl{color:var(--red)}
.value-card{position:absolute;top:376px;width:335px}
.value-card svg{display:block}
.value-card h3{margin-top:18px;font-size:26px;font-weight:700;line-height:32px}
.value-card p{margin-top:14px;font-size:12.8px;line-height:20px}

.map{position:absolute;left:53px;top:2098px;width:513px;height:610px;border-radius:10px;background:linear-gradient(135deg,#e7eaee 0%,#dfe6dc 40%,#eef0f3 60%,#cfe3f3 100%)}
.contact{position:absolute;left:633px;top:2104px;width:514px}
.contact .eyebrow{color:var(--ink)}
.contact h2{margin-top:10px;font-size:40px;line-height:48px;font-weight:700}
.contact .lede{margin-top:16px;font-size:14.5px;line-height:22.5px}
.form-label{display:block;font-size:13px;margin-top:24px}
.field{display:block;width:514px;height:41px;border:1px solid var(--ink);margin-top:9px;background:var(--white)}
.field.area{height:151px;padding:12px 10px;font-size:13px;color:#777}
.consent{display:flex;align-items:center;gap:8px;margin-top:20px;font-size:11.5px}
.box{width:16px;height:16px;border:1px solid var(--ink)}
.consent a{color:var(--red);text-decoration:underline}
.contact .submit{margin-top:28px;width:158px;height:41px}

.site-footer{position:absolute;left:0;top:2852px;width:1200px;height:387px;background:var(--black);color:var(--white)}
.footer-brand{position:absolute;left:60px;top:68px;font-weight:700;font-size:20px;letter-spacing:1px}
.footer-info{position:absolute;left:53px;top:130px;font-size:11.5px;line-height:17px}
.footer-info strong{display:block;font-weight:700}
.footer-info .gap{height:20px}
.footer-nav{position:absolute;left:429px;top:140px;display:flex;gap:27px;font-size:13px;font-weight:500}
.social{position:absolute;left:1068px;top:139px;display:flex;gap:14px}
.social span{width:16px;height:16px;border-radius:50%;background:var(--white)}
.footer-rule{position:absolute;left:53px;top:293px;width:1094px;height:1px;background:var(--line)}
.legal{position:absolute;left:0;top:322px;width:1200px;display:flex;justify-content:center;gap:22px;font-size:11.5px}
.legal a{text-decoration:underline}
</style>
</head>
<body>

<header class="site-header">
  <nav class="main-nav">
    <a href="#">Home</a><a href="#">Services</a><a href="#">Contact Us</a><a href="#" class="current">About Us</a>
  </nav>
  <div class="brand">HALDEN</div>
  <div class="header-phone">
    <svg width="16" height="16" viewBox="0 0 24 24" fill="none" stroke="#fff" stroke-width="2"><path d="M22 16.9v3a2 2 0 0 1-2.2 2 19.8 19.8 0 0 1-8.6-3.1 19.5 19.5 0 0 1-6-6A19.8 19.8 0 0 1 2.1 4.2 2 2 0 0 1 4.1 2h3a2 2 0 0 1 2 1.7c.1.9.4 1.8.7 2.7a2 2 0 0 1-.5 2.1L8 9.8a16 16 0 0 0 6 6l1.3-1.3a2 2 0 0 1 2.1-.4c.9.3 1.8.6 2.7.7a2 2 0 0 1 1.7 2z"/></svg>
    <span>555.201.4410 / 555.308.7215</span>
  </div>
  <a class="btn header-book" href="#">Book an Appointment</a>
</header>

<h1 class="hero-title">Driven by Expertise, Fueled by Excellence: Halden Automotive, Your Trusted Auto Care Partner</h1>
<p class="hero-text">At Halden Automotive, we're not just a locally owned and operated auto repair shop in Carrowfield – we're your dedicated car care partners. Led by an ASE master-certified technician with two decades of experience in Navoro &amp; Omvar dealerships, our commitment extends from routine maintenance to complex engine repairs and hybrid diagnostics. Equipped with state-of-the-art tools, we ensure swift and precise diagnoses, backed by warranties and the convenience of towing. Experience excellence with every service, including special discounts for RideLoop &amp; CityHop rides.</p>

<div class="hero-photo" role="img" aria-label="Four Navoro and Omvar SUVs parked in front of the repair shop building under a blue sky"></div>

<div class="hero-actions">
  <a class="btn" href="#">Schedule</a>
  <a class="learn" href="#">Learn More
    <svg width="8" height="12" viewBox="0 0 8 12" fill="none" stroke="#111" stroke-width="2"><path d="M2 1l5 5-5 5"/></svg>
  </a>
</div>

<section class="values">
  <div class="eyebrow">Our values</div>
  <h2>Guided by Excellence: Our Core Values at Halden Automotive</h2>
  <p class="lede">At <span class="hl">Halden Automotive</span>, our values form the bedrock of our commitment – <span class="hl">Excellence, Integrity, and Customer Satisfaction</span>. We take pride in upholding these principles in every aspect of our auto care services.</p>

  <div class="value-card" style="left:53px">
    <svg width="38" height="38" viewBox="0 0 24 24" fill="#fff"><path d="M22.7 19l-9.1-9.1c.9-2.3.4-5-1.5-6.9-2-2-5-2.4-7.4-1.3L9 6 6 9 1.6 4.7C.4 7.1.9 10.1 2.9 12.1c1.9 1.9 4.6 2.4 6.9 1.5l9.1 9.1c.4.4 1 .4 1.4 0l2.3-2.3c.5-.4.5-1.1.1-1.4z"/></svg>
    <h3>Precision in Every Repair</h3>
    <p>At Halden Automotive, excellence is not just a goal; it's our standard. From routine maintenance to intricate repairs, our commitment to precision ensures your vehicle receives top-notch care, leaving no room for compromise.</p>
  </div>
  <div class="value-card" style="left:431px">
    <svg width="40" height="38" viewBox="0 0 40 38" fill="none" stroke="#fff" stroke-width="3" stroke-linejoin="round"><path d="M3 14l9-7 7 3 8-3 10 7-10 10-6 4-6-4z"/><path d="M19 10l-5 7 4 3 6-6"/></svg>
    <h3>Honesty at the Core</h3>
    <p>Integrity is the foundation of Halden Automotive. We prioritize transparency and honesty in all our interactions. You can trust us to provide straightforward recommendations and fair assessments, ensuring your peace of mind throughout the repair process.</p>
  </div>
  <div class="value-card" style="left:809px">
    <svg width="38" height="38" viewBox="0 0 24 24" fill="#fff"><path d="M12 1.5l3.2 6.8 7.3.9-5.4 5 1.4 7.3L12 17.9l-6.5 3.6 1.4-7.3-5.4-5 7.3-.9z"/></svg>
    <h3>Customer Satisfaction</h3>
    <p>Customer satisfaction is our driving force. We go the extra mile to ensure your experience with Halden Automotive is not only about fixing your vehicle but also about exceeding your expectations. Your trust and satisfaction are our ultimate rewards.</p>
  </div>
</section>

<div class="map" role="img" aria-label="Street map showing the shop location, Suite 5, in Carrowfield"></div>

<section class="contact">
  <div class="eyebrow">Contact Us</div>
  <h2>Expert Auto Repair Services Available</h2>
  <p class="lede"><strong class="hl" style="font-weight:500">Contact us for a free estimate!</strong> Please include year, make and model and the service or repair you would like an estimate on.</p>
  <label class="form-label">Name</label>
  <div class="field"></div>
  <label class="form-label" style="margin-top:29px">Phone Number</label>
  <div class="field"></div>
  <label class="form-label" style="margin-top:29px">Message</label>
  <div class="field area">Type your message...</div>
  <div class="consent"><span class="box"></span><span>I accept the <a href="#">Terms</a></span></div>
  <a class="btn submit" href="#">Get a Free Estimate</a>
</section>

<footer class="site-footer">
  <div class="footer-brand">HALDEN</div>
  <div class="footer-info">
    <strong>Address:</strong>
    <div style="margin-top:4px">412 Ridgeline Court #5 Carrowfield, TX 75090</div>
    <div class="gap"></div>
    <strong>Contact:</strong>
    <div style="margin-top:4px">Office Number - 555.201.4410</div>
    <div>Cell Number - 555.308.7215</div>
  </div>
  <nav class="footer-nav">
    <a href="#">HOME</a><a href="#">SERVICES</a><a href="#">CONTACT US</a><a href="#">ABOUT US</a>
  </nav>
  <div class="social"><span></span><span></span><span></span></div>
  <div class="footer-rule"></div>
  <div class="legal">
    <span>© 2024 Halden Automotive. All rights reserved.</span>
    <a href="#">Privacy Policy</a><a href="#">Terms of Service</a><a href="#">Cookies Settings</a>
  </div>
</footer>

</body>
</html>
```